Corvina Dental personal information forms

We are a Dental Practice that require an update to our information forms, there are 3 versions of it.
I will attach our old ones, we need to keep the same information on there, we just want them to look better and use our current logo and colours.
Our website is www.corvinadental.net
Our facebook is www.friendspage.net/corvinadentalbelmorewalk/
..................................................................................................

Target Market(s)

Everyone, easy to read

Industry/Entity Type

Dental Clinic

Colors
0692cd
34a6d7
cee9f5
ffffff
0255a3
3276b5

Requirements
Must have
• Logo
• Our colours
• same information as the uploaded versions
Should not have
• any other colour besides the blues, black and white

```html
<!DOCTYPE html>
<html lang="en">
<head>
<meta charset="utf-8">
<title>Corvina Dental – Patient Information Update</title>
<link href="https://fonts.googleapis.com/css2?family=Open+Sans:wght@400;600;700&display=swap" rel="stylesheet">
<style>
:root{
  --blue-deep:#0255a3;
  --blue-main:#0692cd;
  --blue-mid:#3276b5;
  --blue-light:#34a6d7;
  --blue-pale:#cee9f5;
  --white:#ffffff;
  --ink:#111111;
  --rule:#c9cfd6;
  --field:#ececec;
  --backdrop:#f2f4f6;
}
*{box-sizing:border-box;margin:0;padding:0}
html,body{width:1200px;height:1200px;overflow:hidden;background:var(--backdrop);font-family:"Open Sans",Arial,sans-serif;color:var(--ink)}
.sheet{position:absolute;left:211px;top:50px;width:778px;height:1100px;overflow:hidden;background:var(--white);display:flex;flex-direction:column}
.masthead{height:70px;flex:none;background:linear-gradient(90deg,var(--blue-deep),var(--blue-main) 50%,var(--blue-deep));display:flex;align-items:center;justify-content:center}
.brand{color:var(--white);font-size:32px;font-weight:600;letter-spacing:.5px}
.masthead-rules{height:10px;flex:none;border-top:4px solid var(--white);border-bottom:3px solid var(--blue-main);background:var(--white)}
.intro{padding:12px 22px 8px 22px;flex:none}
.doctor{color:var(--blue-deep);font-weight:700;font-size:15px;line-height:19px}
.welcome{color:var(--blue-main);font-size:15px;line-height:20px;margin-top:9px}
.notice{font-size:13px;line-height:17px;margin-top:4px}
.notice b{font-weight:700}
.records{margin:4px 10px 0 10px;border:1px solid var(--rule);border-top:none;flex:none}
.tabs{display:flex;height:22px;background:linear-gradient(90deg,var(--blue-deep),var(--blue-main) 50%,var(--blue-deep));border-radius:12px 12px 0 0}
.tab{color:var(--white);font-weight:700;font-size:12px;display:flex;align-items:center;justify-content:center}
.tab.patient{width:59%}.tab.contact{width:41%}
.records-body{display:flex;padding:4px 10px 10px 10px;gap:14px}
.col-patient{width:436px}
.col-contact{flex:1}
.titles{display:flex;gap:22px;font-size:11.5px;line-height:14px;padding:4px 8px 6px}
table{border-collapse:collapse;width:100%;font-size:10.5px}
td{border:1px solid var(--rule);height:19.5px;padding:0 7px;vertical-align:middle;line-height:12px}
td.label{width:92px}
td.nolines{border-top:none;border-bottom:none}
.post{width:92px}
.contact-table{margin-top:24px}
.contact-table td.label{width:78px}
.methods{display:flex;justify-content:space-around;padding:0 8px}
.referred{font-size:10.5px;line-height:12px;padding:4px 0}
.emergency-head{background:linear-gradient(90deg,var(--blue-deep),var(--blue-main));color:var(--white);font-weight:700;font-size:11.5px;text-align:center;height:19px;line-height:19px}
.emergency td.label{width:110px}
.questions{margin:0 10px;border:1px solid var(--rule);border-top:none;padding:8px 10px 8px 10px;font-size:11px;line-height:14px;flex:none}
.question{display:flex;justify-content:space-between;padding:0 6px 3px 6px}
.yn{font-weight:700}
.answer{height:22px;background:var(--field);border:1px solid #dcdcdc;margin-bottom:10px}
.conditions{display:grid;grid-template-columns:236px 240px 1fr;padding:4px 24px 8px;font-size:11.3px}
.item{display:flex;align-items:center;gap:11px;height:17.5px}
.box{width:8px;height:8px;border:1.5px solid var(--ink);border-top-width:1px;border-left-width:1px;flex:none}
.declaration{padding:9px 18px 0;font-size:9.3px;line-height:11.5px;flex:none}
.declaration .lead{font-weight:700;margin-bottom:5px}
.signoff{display:flex;gap:34px;padding:12px 18px 0;font-size:10.5px;line-height:13px;flex:none}
.line{display:inline-block;border-bottom:1px solid #999;width:130px;margin-left:4px}
.foot{margin-top:auto;height:16px;flex:none;background:linear-gradient(90deg,var(--blue-deep),var(--blue-main) 50%,var(--blue-deep));border-top:4px solid var(--white);box-shadow:0 -3px 0 var(--blue-main)}
</style>
</head>
<body>
<main class="sheet">
  <header class="masthead"><span class="brand">Corvina Dental</span></header>
  <div class="masthead-rules"></div>

  <section class="intro">
    <p class="doctor">Dr. Elias Varnecki<br>Dental Surgeon</p>
    <p class="welcome">Welcome back to our practice!</p>
    <p class="notice"><b>THIS INFORMATION IS CONFIDENTIAL</b> and is necessary to enable us to offer you <b>THE BEST POSSIBLE CARE</b>. Because we haven't seen you in some time and because we care about your health status, Please take you time and thoroughly complete the following update of your personal and medical information It is <b>essential</b> that we know about your past and present medical history. Many medical conditions may interfere with dental procedures.</p>
  </section>

  <section class="records">
    <div class="tabs"><div class="tab patient">PATIENT INFORMATION</div><div class="tab contact">PATIENT CONTACT INFORMATION</div></div>
    <div class="records-body">
      <div class="col-patient">
        <div class="titles"><span>Ms</span><span>Mrs</span><span>Miss</span><span>Mr</span><span>Master</span><span>Dr</span><span>Other</span></div>
        <table class="patient-table">
          <tr><td class="label">Surname</td><td colspan="2"></td></tr>
          <tr><td class="label">First name</td><td colspan="2"></td></tr>
          <tr><td class="label">Preferred</td><td colspan="2"></td></tr>
          <tr><td class="label">Date of birth</td><td colspan="2"></td></tr>
          <tr><td class="label nolines" style="border-top:1px solid var(--rule)">Current</td><td colspan="2"></td></tr>
          <tr><td class="label nolines">Residental</td><td colspan="2"></td></tr>
          <tr><td class="label nolines" style="border-bottom:1px solid var(--rule)">Address</td><td></td><td class="post">Postcode:</td></tr>
          <tr><td class="label nolines">Postal</td><td colspan="2"></td></tr>
          <tr><td class="label nolines">Residental</td><td colspan="2"></td></tr>
          <tr><td class="label nolines">Address</td><td colspan="2"></td></tr>
          <tr><td class="label nolines" style="border-bottom:1px solid var(--rule)">(If different)</td><td></td><td class="post">Postcode:</td></tr>
          <tr><td class="label">Occupation</td><td colspan="2"></td></tr>
          <tr><td class="label">Employer</td><td colspan="2"></td></tr>
        </table>
      </div>
      <div class="col-contact">
        <table class="contact-table">
          <tr><td class="label nolines" style="border-top:1px solid var(--rule)">Phone</td><td>M:</td></tr>
          <tr><td class="label nolines"></td><td>H:</td></tr>
          <tr><td class="label nolines" style="border-bottom:1px solid var(--rule)"></td><td>W:</td></tr>
          <tr><td class="label">Email</td><td></td></tr>
          <tr><td class="label">Preferred</td><td></td></tr>
          <tr><td colspan="2">Preferred method of communication:</td></tr>
          <tr><td colspan="2"><div class="methods"><span>SMS</span><span>Phone</span><span>Email</span><span>Mail</span></div></td></tr>
        </table>
        <p class="referred">Referred by:</p>
        <div class="emergency-head">EMERGENCY CONTACT</div>
        <table class="emergency">
          <tr><td class="label">Name</td><td></td></tr>
          <tr><td class="label">Relationship</td><td></td></tr>
          <tr><td class="label nolines" style="border-top:1px solid var(--rule)">Contact</td><td rowspan="2"></td></tr>
          <tr><td class="label nolines" style="border-bottom:1px solid var(--rule)">Number</td></tr>
        </table>
      </div>
    </div>
  </section>

  <section class="questions">
    <div class="question"><span>Have you taken any prescribed medication or dietory supplements in the lost 12 months?(If yes,please list below)</span><span class="yn">YES/NO</span></div>
    <div class="answer"></div>
    <div class="question"><span>Allergies/Reactions? If yes, Please list below:</span><span class="yn">YES/NO</span></div>
    <div class="answer"></div>
    <div class="question"><span>Have you ever had or are you suffering from any of the following? Please tick any that apply :</span></div>
    <div class="conditions">
      <div class="item"><span class="box"></span>Rheumatic fever</div>
      <div class="item"><span class="box"></span>Diabetes</div>
      <div class="item"><span class="box"></span>HIV Positive</div>
      <div class="item"><span class="box"></span>Epilepsy</div>
      <div class="item"><span class="box"></span>kidney disease</div>
      <div class="item"><span class="box"></span>High cholesterol</div>
      <div class="item"><span class="box"></span>Asthma</div>
      <div class="item"><span class="box"></span>Heart attack</div>
      <div class="item"><span class="box"></span>Cancer</div>
      <div class="item"><span class="box"></span>Tuberculosis</div>
      <div class="item"><span class="box"></span>High Blood Pressure</div>
      <div class="item"><span class="box"></span>Pace-maker</div>
      <div class="item"><span class="box"></span>Radiation Therapy</div>
      <div class="item"><span class="box"></span>Bleeding problems</div>
      <div class="item"><span class="box"></span>Osteoporosis</div>
      <div class="item"><span class="box"></span>Dizziness, fainting</div>
      <div class="item"><span class="box"></span>Artificial joints</div>
      <div class="item"><span class="box"></span>Heart rate problems</div>
      <div class="item"><span class="box"></span>Hepatitis A B or C</div>
      <div class="item"><span class="box"></span>Respiratory Problems</div>
      <div class="item"><span class="box"></span>Heart murmur</div>
    </div>
    <div class="question"><span>Do you have any disease,condition or problem not lited above?</span><span class="yn">YES/NO</span></div>
    <div class="answer"></div>
    <div class="question"><span>Have you had surgery or been to hospital in the last 5 years? (If YES,Please give details)</span><span class="yn">YES/NO</span></div>
    <div class="answer"></div>
    <div class="question"><span>For Women:Are you pregnant? (If YES, How many months?)</span><span class="yn">YES/NO</span></div>
    <div class="answer" style="margin-bottom:0"></div>
  </section>

  <section class="declaration">
    <p class="lead">The information that I have provided is to the best of my knowledge true and I understand that is my responsibility to inform of any changes in my medical status.</p>
    <p>This is to certify that I, the undersigned, consent to the performing of the dental and oral surgery procedures agreed to be necessary or advisable, including the use of local anaesthetic as indicated and I will assume responsibility for the fees associated with these procedures.Therefore, I shall pay any legal costs, including solicitor and own costs, tracing costs and any collection commission incurred by Corvina Dental as a result of my failure to pay any amount due to Corvina Dental.</p>
  </section>
  <div class="signoff"><span>Patient/Parent/Person Responsible signature:<span class="line"></span></span><span>Date:<span class="line"></span></span></div>

  <footer class="foot"></footer>
</main>
</body>
</html>
```